New Innovative Counselling and psychotherapy Service needs Business Card design

Keep it simple and professional. On one side, just company name and logo (perhaps in all blue) and maybe a tag line.

On other side (all white) my name and Qualifications in centre

Industry/Entity Type

Health And Wellness

Contact Information for Business Card

Dara Whelby
Counsellor & Psychotherapist
BSc (Psychol.), BA, Dip. (Couns. & Psych.), PG.Cert (CBT), FGTrK, ONRE

I will also require Mobile no, Email and web site address of which I'll pass on to final designer.

Font styles to use
Sans Serif

Requirements
Must have
• My Logo Only and please use the colours in logo that is in it.
Should not have
• Any other images

```html
<!DOCTYPE html>
<html lang="en">
<head>
<meta charset="utf-8">
<title>Thrive Harbour – Business Card</title>
<link rel="stylesheet" href="https://fonts.googleapis.com/css2?family=Raleway:wght@300;400&family=Arimo:wght@400;700&display=swap">
<style>
  :root {
    --sky: #52b7ec;
    --sky-deep: #3fa4dc;
    --leaf: #8cc84b;
    --ink: #333a40;
    --paper: #ffffff;
    --backdrop: #e6e7e8;
    --teal: #2fa7a0;
  }
  * { box-sizing: border-box; margin: 0; padding: 0; }
  html, body {
    width: 1200px; height: 726px; overflow: hidden;
    background: var(--backdrop);
  }
  .canvas { position: relative; width: 1200px; height: 726px; }

  .card {
    position: absolute;
    width: 540px; height: 309px;
    overflow: hidden;
    box-shadow: 0 6px 18px rgba(0,0,0,.12);
  }

  /* Front */
  .card--front {
    left: 40px; top: 150px;
    background: var(--sky);
    display: flex; align-items: center; justify-content: center;
  }
  .front-brand { display: flex; align-items: center; gap: 18px; }
  .brand-dot {
    width: 54px; height: 54px; border-radius: 50%;
    background: var(--paper);
  }
  .front-name {
    font-family: "Raleway", sans-serif; font-weight: 300;
    font-size: 40px; color: var(--paper); line-height: 1;
  }
  .front-tagline {
    font-family: "Arimo", sans-serif; font-size: 13px;
    letter-spacing: 0.42em; color: var(--paper);
    margin-top: 8px; padding-left: 4px;
  }

  /* Back */
  .card--back {
    left: 620px; top: 256px;
    background: var(--paper);
  }
  .back-circle {
    position: absolute; right: -110px; top: -40px;
    width: 300px; height: 300px; border-radius: 50%;
    background: var(--sky-deep);
  }
  .back-content { position: absolute; left: 34px; top: 52px; }
  .back-brand { display: flex; align-items: center; gap: 12px; }
  .back-brand .brand-dot {
    width: 50px; height: 50px; background: var(--sky-deep);
  }
  .back-name {
    font-family: "Raleway", sans-serif; font-weight: 400;
    font-size: 27px; line-height: 1.0; color: var(--ink);
  }
  .person {
    margin-top: 26px;
    font-family: "Arimo", sans-serif; font-weight: 700;
    font-size: 20px; color: var(--sky-deep);
  }
  .credentials {
    margin-top: 4px;
    font-family: "Arimo", sans-serif; font-size: 11.5px;
    line-height: 1.35; color: var(--ink); width: 270px;
  }
  .contacts { margin-top: 14px; list-style: none; }
  .contacts li {
    display: flex; align-items: center; gap: 8px;
    font-family: "Arimo", sans-serif; font-size: 13px;
    color: var(--ink); line-height: 1.5;
  }
  .contacts svg { width: 12px; height: 12px; flex: none; }
</style>
</head>
<body>
<main class="canvas">

  <section class="card card--front" aria-label="Card front">
    <div class="front-brand">
      <span class="brand-dot" aria-hidden="true"></span>
      <div>
        <div class="front-name">Thrive Harbour</div>
        <div class="front-tagline">A tag line goes here</div>
      </div>
    </div>
  </section>

  <section class="card card--back" aria-label="Card back">
    <span class="back-circle" aria-hidden="true"></span>
    <div class="back-content">
      <div class="back-brand">
        <span class="brand-dot" aria-hidden="true"></span>
        <div class="back-name">Thrive<br>Harbour</div>
      </div>
      <div class="person">Dara Whelby</div>
      <p class="credentials">Counsellor &amp; Psychotherapist<br>BSc (Psychol.), BA, Dip. (Couns. &amp; Psych.), PG.Cert (CBT), FGTrK, ONRE</p>
      <ul class="contacts">
        <li>
          <svg viewBox="0 0 12 12" aria-hidden="true"><path fill="var(--teal)" d="M1 4c0-2 2-3 5-3s5 1 5 3l-2 1-1-1.5H4L3 5zM3 6h6l1 5H2z"/></svg>
          0123 456 7890
        </li>
        <li>
          <svg viewBox="0 0 12 12" aria-hidden="true"><rect x="0.5" y="2" width="11" height="8" fill="var(--leaf)"/><path d="M1 2.5l5 4 5-4" fill="none" stroke="#fff" stroke-width="1"/></svg>
          dara.w@ThriveHarbour.com
        </li>
        <li>
          <svg viewBox="0 0 12 12" aria-hidden="true"><circle cx="6" cy="6" r="5.5" fill="var(--leaf)"/><path d="M0.5 6h11M6 .5c-2.5 3-2.5 8 0 11M6 .5c2.5 3 2.5 8 0 11" fill="none" stroke="#fff" stroke-width=".8"/></svg>
          www.ThriveHarbour.com
        </li>
      </ul>
    </div>
  </section>

</main>
</body>
</html>
```